Design for schnapps bottle label "Río Ámbar"

Hi! On a small land lot we are producing our own Italian schnapps "Grappa". For the bottles we would like to modernize our current labes that you find below. The two cats looking at each other should remain, but updated and more modern. I am very much looking forward to your suggestions. Best, Jens

Target Market(s)

Schnapps bottle label

Requirements
Must have
• Cats should resemble the cats that are decorating the house entry (see attached), however, should have a more modern appearance.

Text elements should remain: "Grappa", "Río Ámbar", "Legnoso", "[Vintage Year], "Raccolta No", "Vol %"
Should not have
• Current ornament can be used, replaced or deleted (whatever looks best)

```html
<!DOCTYPE html>
<html lang="it">
<head>
<meta charset="utf-8">
<title>Grappa legnoso 2015 – Río Ámbar</title>
<link rel="stylesheet" href="https://fonts.googleapis.com/css2?family=Berkshire+Swash&family=Parisienne&family=Cormorant+Garamond:wght@500&family=Federo&display=swap">
<style>
  :root {
    --backdrop: #352a22;
    --label-black: #141414;
    --label-black-soft: #1c1c1c;
    --accent-orange: #e8762c;
    --accent-copper: #b5652a;
    --accent-red: #d93a22;
    --band-orange: #ef8a2e;
    --band-red: #e0472a;
    --text-white: #ffffff;
    --outline-brown: #8a4a1e;
  }
  * { margin: 0; padding: 0; box-sizing: border-box; }
  html, body {
    width: 900px; height: 1200px; overflow: hidden;
    background: var(--backdrop);
  }
  .canvas {
    position: relative;
    width: 900px; height: 1200px;
    background: var(--backdrop);
  }
  .label {
    position: absolute;
    left: 186px; top: 40px;
    width: 528px; height: 1120px;
  }
  .label-top-rule {
    position: absolute; left: 0; top: 0; width: 100%; height: 9px;
    background: linear-gradient(90deg, var(--accent-orange), var(--accent-copper), var(--accent-orange));
  }
  .label-panel {
    position: absolute; left: 0; top: 9px; width: 100%; height: 956px;
    background: radial-gradient(ellipse at 50% 40%, var(--label-black-soft), var(--label-black));
  }
  .label-bottom-rule {
    position: absolute; left: 0; top: 963px; width: 100%; height: 6px;
    background: linear-gradient(90deg, var(--accent-orange), var(--accent-copper), var(--accent-orange));
  }
  .label-band {
    position: absolute; left: 0; top: 980px; width: 100%; height: 140px;
    background: linear-gradient(90deg, var(--band-red) 0%, var(--band-orange) 35%, var(--band-orange) 65%, var(--band-red) 100%);
  }
  .product-name {
    position: absolute; left: 0; top: 70px; width: 100%;
    text-align: center;
    font-family: "Berkshire Swash", serif;
    font-size: 150px; line-height: 1;
    color: var(--text-white);
    -webkit-text-stroke: 2px var(--outline-brown);
    paint-order: stroke fill;
  }
  .edition {
    position: absolute; left: 0; top: 292px; width: 100%;
    text-align: center; color: var(--accent-orange);
  }
  .edition-style {
    font-family: "Parisienne", cursive;
    font-size: 42px;
  }
  .edition-year {
    font-family: "Cormorant Garamond", serif;
    font-size: 34px; font-weight: 500;
  }
  .edition-of {
    position: absolute; left: 0; top: 362px; width: 100%;
    text-align: center;
    font-family: "Parisienne", cursive;
    font-size: 30px; color: var(--accent-orange);
  }
  .cats-art {
    position: absolute; left: 35px; top: 437px;
    width: 457px; height: 182px;
  }
  .producer {
    position: absolute; left: 0; top: 690px; width: 100%;
    text-align: center;
    font-family: "Federo", sans-serif;
    font-size: 88px; line-height: 1.2;
    color: var(--accent-red);
  }
  .batch {
    position: absolute; left: 24px; top: 908px;
    color: var(--accent-orange);
    font-size: 34px;
  }
  .batch-word { font-family: "Parisienne", cursive; }
  .batch-number { font-family: "Federo", sans-serif; font-size: 30px; }
  .strength {
    position: absolute; right: 22px; top: 908px;
    color: var(--accent-orange);
    font-family: "Federo", sans-serif;
    font-size: 28px;
  }
  .strength-unit { font-family: "Parisienne", cursive; font-size: 34px; }
</style>
</head>
<body>
<main class="canvas">
  <section class="label">
    <div class="label-top-rule"></div>
    <div class="label-panel"></div>

    <h1 class="product-name">Grappa</h1>
    <p class="edition"><span class="edition-style">“legnoso”</span><span class="edition-year">2015</span></p>
    <p class="edition-of">di</p>

    <svg class="cats-art" viewBox="0 0 457 182" role="img" aria-label="Illustration of two white cat silhouettes crouching and facing each other, tails curled upward">
      <rect x="0" y="0" width="457" height="182" rx="10" fill="#ececec"/>
    </svg>

    <p class="producer">Río Ámbar</p>

    <p class="batch"><span class="batch-word">Raccolta No.</span> <span class="batch-number">01</span></p>
    <p class="strength">41.0 <span class="strength-unit">Vol</span></p>

    <div class="label-bottom-rule"></div>
    <div class="label-band" role="img" aria-label="Decorative orange and red pattern band with cat silhouettes"></div>
  </section>
</main>
</body>
</html>
```